Vento Hallmark Real estate Costa del sol

we need a website for our Company based in Costa del sol, Spain. We sell properties on the spanish coast that is called costa del sol. We are concentrating on exclusive properties and would like the webdesign to show this. In our website we want to have area descriptions of the different areas we sell our Products. We will also implement a searchable database delivered by a third part where all properties for sale in Spain are listed. When looking into the designs we would like our main page to have a overview of the coast where the different areas are shown. Have a look at brightlunavista.example or oakterra.example to see. The webpage will be presented in 4 languages, English, spanish, Swedish and norwegian, and shall of course also be prepared for social medias. We want an easy Contemporary design but still with an exclusive feeling!
Scandinavian and North european Citizens wants to buy a property in Spain
Real Estate
5+ page

```html
<!DOCTYPE html>
<html lang="en">
<head>
<meta charset="utf-8">
<title>Vento Hallmark – Costa del Sol Real Estate</title>
<link href="https://fonts.googleapis.com/css2?family=Open+Sans:wght@400;600&display=swap" rel="stylesheet">
<style>
:root{
  --navy:#0b0c35;
  --navy-band:rgba(22,26,72,.95);
  --ink:#1d1d2b;
  --muted:#9a9a9a;
  --light:#f2f2f2;
  --white:#ffffff;
  --footer:#262626;
  --footer-bottom:#1c1c1c;
  --footer-text:#b5b5b5;
  --btn-grey:#a6a6a6;
}
*{box-sizing:border-box;margin:0;padding:0}
html,body{width:782px;height:1200px;overflow:hidden;background:var(--white)}
body{position:relative;font-family:'Open Sans',Arial,sans-serif;color:var(--ink)}
.abs{position:absolute}
h2,h3,h4{font-weight:400}

/* header */
.brand{left:86px;top:14px;display:flex;flex-direction:column;align-items:center;width:118px}
.brand-mark{width:40px;height:40px;border:5px solid var(--navy);margin-bottom:5px}
.brand-name{font-size:18px;color:#2a2a3a;letter-spacing:.2px;white-space:nowrap}
.call{left:510px;top:19px;text-align:right;width:82px;line-height:1.15}
.call small{display:block;font-size:7.5px;color:#555}
.call strong{font-weight:400;font-size:10.5px;color:#222}
.phone-badge{left:595px;top:21px;width:19px;height:19px;border-radius:50%;background:var(--navy)}
.lang{left:627px;top:20px;width:69px;height:20px;border:1px solid #d8d8d8;font-size:7px;color:#666;display:flex;align-items:center;padding-left:8px;gap:4px}
.lang .flag{width:8px;height:6px;background:#c8102e}
.lang svg{margin-left:auto;margin-right:7px}
.nav{left:460px;top:70px;display:flex;gap:20px;font-size:8px;color:#222}

/* hero */
.hero{left:0;top:99px;width:782px;height:224px;
  background:
    linear-gradient(180deg,rgba(0,0,0,0) 70%,rgba(30,40,60,.35) 100%),
    linear-gradient(105deg,#17171c 0%,#2b2a2e 22%,#57524b 40%,#8d877c 52%,#c9cdd0 64%,#e6eaed 74%,#6f7f6a 86%,#3f6688 100%)}
.search{left:0;top:323px;width:782px;height:76px;background:var(--navy-band)}
.search h2{position:absolute;top:12px;width:100%;text-align:center;color:var(--white);font-weight:600;font-size:15px;letter-spacing:.2px}
.field{top:360px;height:26px;background:var(--white);font-size:7.5px;color:#444;display:flex;align-items:center;padding:0 8px 0 11px;justify-content:space-between}
.search-btn{left:666px;top:360px;width:29px;height:26px;background:var(--btn-grey);display:flex;align-items:center;justify-content:center}

/* sections */
.section-title{font-size:18px;color:#111;letter-spacing:.2px}
.pager{display:flex;gap:4px}
.pager span{width:15px;height:13px;border:1px solid #bbb;display:flex;align-items:center;justify-content:center}
.card{width:142px;height:156px}
.card .photo{height:104px}
.card .caption{height:52px;background:var(--navy);color:var(--white);text-align:center;font-size:7.2px;font-weight:400;line-height:1.45;padding-top:9px}
.card .price{display:block;margin-top:3px;font-weight:600}

.blog-band{left:0;top:643px;width:782px;height:156px;background:var(--light)}
.blog-title{left:86px;top:662px;font-size:17px;color:#111}
.view-all{left:663px;top:667px;width:32px;height:12px;background:#3a3a3a;color:var(--white);font-size:5.5px;display:flex;align-items:center;justify-content:center}
.post-photo{width:116px;height:84px;top:693px}
.post-text{top:692px;width:165px}
.post-text time{font-size:7.5px;color:#222;display:block}
.post-text h3{font-size:9.6px;line-height:1.45;color:#222;margin-top:6px}
.post-text p{font-size:5.2px;line-height:1.6;color:var(--muted);margin-top:6px}
.post-text p b{color:#222;font-weight:600}

/* footer */
.footer{left:0;top:1054px;width:782px;height:115px;background:var(--footer)}
.foot-head{top:1075px;font-size:9.5px;color:#e5e5e5}
.foot-list{top:1094px;font-size:6.5px;color:var(--footer-text);line-height:2;list-style:none}
.news-input{left:362px;top:1097px;width:141px;height:26px;background:var(--white);font-size:6.5px;color:#888;display:flex;align-items:center;padding-left:12px}
.news-btn{left:503px;top:1097px;width:52px;height:26px;background:var(--navy);color:var(--white);font-size:8px;display:flex;align-items:center;justify-content:center}
.social{left:613px;top:1096px;display:flex;gap:5px}
.social span{width:17px;height:17px;border-radius:50%}
.copy{left:0;top:1169px;width:782px;height:31px;background:var(--footer-bottom);color:#bdbdbd;font-size:6.5px;display:flex;align-items:center;justify-content:center}
</style>
</head>
<body>

<header>
  <div class="abs brand"><span class="brand-mark"></span><span class="brand-name">Vento Hallmark</span></div>
  <div class="abs call"><small>Call us on</small><strong>612 480 9273</strong></div>
  <div class="abs phone-badge">
    <svg width="19" height="19" viewBox="0 0 19 19"><rect x="7" y="5" width="5" height="9" rx="1" fill="none" stroke="#fff" stroke-width="1.3"/></svg>
  </div>
  <div class="abs lang"><span class="flag"></span>English
    <svg width="6" height="4" viewBox="0 0 6 4"><path d="M.5.5 3 3 5.5.5" fill="none" stroke="#777"/></svg>
  </div>
  <nav class="abs nav"><span>Home</span><span>Costa del sol</span><span>Services</span><span>Blog</span><span>Contact Us</span></nav>
</header>

<div class="abs hero" role="img" aria-label="Modern luxury villa with terrace loungers and an infinity pool overlooking wooded hills"></div>
<svg class="abs" style="left:4px;top:199px" width="8" height="14" viewBox="0 0 8 14"><path d="M7 1 1 7l6 6" fill="none" stroke="#fff" stroke-width="1"/></svg>
<svg class="abs" style="left:766px;top:199px" width="16" height="22" viewBox="0 0 16 22"><rect width="16" height="22" fill="rgba(120,120,120,.6)"/><path d="M5 5l6 6-6 6" fill="none" stroke="#fff" stroke-width="1"/></svg>

<section class="abs search"><h2>SEARCH PROPERTY</h2></section>
<div class="abs field" style="left:86px;width:143px">Location
  <svg width="6" height="8" viewBox="0 0 6 8"><path d="M3 8C1 5 0 4 0 3a3 3 0 0 1 6 0c0 1-1 2-3 5z" fill="#333"/><circle cx="3" cy="3" r="1" fill="#fff"/></svg></div>
<div class="abs field" style="left:238px;width:143px">Type
  <svg width="6" height="4" viewBox="0 0 6 4"><path d="M.5.5 3 3 5.5.5" fill="none" stroke="#444"/></svg></div>
<div class="abs field" style="left:390px;width:143px">Price range
  <svg width="6" height="4" viewBox="0 0 6 4"><path d="M.5.5 3 3 5.5.5" fill="none" stroke="#444"/></svg></div>
<div class="abs field" style="left:542px;width:55px">Beds
  <svg width="6" height="4" viewBox="0 0 6 4"><path d="M.5.5 3 3 5.5.5" fill="none" stroke="#444"/></svg></div>
<div class="abs field" style="left:604px;width:55px">Baths
  <svg width="6" height="4" viewBox="0 0 6 4"><path d="M.5.5 3 3 5.5.5" fill="none" stroke="#444"/></svg></div>
<div class="abs search-btn">
  <svg width="11" height="11" viewBox="0 0 11 11"><circle cx="4.5" cy="4.5" r="3.3" fill="none" stroke="#fff" stroke-width="1.6"/><path d="M7 7l3 3" stroke="#fff" stroke-width="1.8"/></svg>
</div>

<!-- featured -->
<h2 class="abs section-title" style="left:85px;top:430px">FEATURED PROPERTIES</h2>
<div class="abs pager" style="left:660px;top:435px">
  <span><svg width="4" height="6" viewBox="0 0 4 6"><path d="M3.5.5 1 3l2.5 2.5" fill="none" stroke="#888"/></svg></span>
  <span><svg width="4" height="6" viewBox="0 0 4 6"><path d="M.5.5 3 3 .5 5.5" fill="none" stroke="#888"/></svg></span>
</div>
<article class="abs card" style="left:86px;top:463px"><div class="photo" role="img" aria-label="White modern villa with lawn and paved drive under blue sky" style="background:linear-gradient(165deg,#3f78c4 0%,#9ab8dc 30%,#eef0ef 48%,#b8b4ad 62%,#6d8f45 80%,#8a4a3a 100%)"></div><div class="caption">Curabitur nisl ex, auctor in nisl in,<br>interdum porta urna<span class="price">1.250.000 €</span></div></article>
<article class="abs card" style="left:242px;top:463px"><div class="photo" role="img" aria-label="White contemporary house with timber deck among tall trees" style="background:linear-gradient(180deg,#2f4a2c 0%,#5d7550 22%,#f2f2f0 45%,#d9d8d4 62%,#7a5638 80%,#5f7a3e 100%)"></div><div class="caption">Curabitur nisl ex, auctor in nisl in,<br>interdum porta urna<span class="price">1.250.000 €</span></div></article>
<article class="abs card" style="left:398px;top:463px"><div class="photo" role="img" aria-label="Villa entrance with lit pathway and planters at dusk" style="background:linear-gradient(180deg,#9fb2c8 0%,#dfe4ea 28%,#f6f3ea 50%,#8d8f90 70%,#3d4344 100%)"></div><div class="caption">Curabitur nisl ex, auctor in nisl in,<br>interdum porta urna<span class="price">1.250.000 €</span></div></article>
<article class="abs card" style="left:553px;top:463px"><div class="photo" role="img" aria-label="Sandstone townhouse with garage doors and glass balcony" style="background:linear-gradient(180deg,#dfe7ee 0%,#d8c3a2 28%,#c49a68 52%,#9e7c58 72%,#6e6a66 100%)"></div><div class="caption">Curabitur nisl ex, auctor in nisl in,<br>interdum porta urna<span class="price">1.250.000 €</span></div></article>

<!-- blog -->
<section class="abs blog-band"></section>
<h2 class="abs blog-title">Blog</h2>
<div class="abs view-all">View All</div>
<div class="abs post-photo" style="left:86px;background:linear-gradient(135deg,#f4f4f2 0%,#dfe1e3 45%,#9aa7bd 80%,#5e6c8a 100%)" role="img" aria-label="Hands signing a property contract beside a small model house"></div>
<div class="abs post-text" style="left:210px"><time>23 September, 2016</time><h3>Donec ultrices in lorem eu dignis-sim. Suspendisse tortor urna, lacinia et aliquam nec, aliquet et.</h3><p>Proin porta fermentum ipsum, vel porttitor turpis venenatis luctus. Vivamus volutpat eu sapien quis tempus. <b>More</b></p></div>
<div class="abs post-photo" style="left:409px;background:linear-gradient(110deg,#3d3f46 0%,#8e8a84 30%,#f3f1ec 55%,#e6d8c6 75%,#b99b7e 100%)" role="img" aria-label="Estate agent meeting a couple at an office table"></div>
<div class="abs post-text" style="left:533px"><time>23 September, 2016</time><h3>Donec ultrices in lorem eu dignis-sim. Suspendisse tortor urna, lacinia et aliquam nec, aliquet et.</h3><p>Proin porta fermentum ipsum, vel porttitor turpis venenatis luctus. Vivamus volutpat eu sapien quis tempus. <b>More</b></p></div>

<!-- latest -->
<h2 class="abs section-title" style="left:85px;top:832px">LATEST PROPERTIES</h2>
<div class="abs pager" style="left:660px;top:837px">
  <span><svg width="4" height="6" viewBox="0 0 4 6"><path d="M3.5.5 1 3l2.5 2.5" fill="none" stroke="#888"/></svg></span>
  <span><svg width="4" height="6" viewBox="0 0 4 6"><path d="M.5.5 3 3 .5 5.5" fill="none" stroke="#888"/></svg></span>
</div>
<article class="abs card" style="left:86px;top:865px"><div class="photo" role="img" aria-label="Modern white villa with stone wall, palm and green lawn" style="background:linear-gradient(180deg,#3a78c8 0%,#a9c6e4 25%,#f1f2f0 45%,#7f8a8c 62%,#5f9a2c 80%,#4a7f22 100%)"></div><div class="caption">Curabitur nisl ex, auctor in nisl in,<br>interdum porta urna<span class="price">1.250.000 €</span></div></article>
<article class="abs card" style="left:242px;top:865px"><div class="photo" role="img" aria-label="Tropical house with dark roof and stepping stones through the garden" style="background:linear-gradient(180deg,#f3f4f2 0%,#4c4744 28%,#e8e8e4 48%,#6f8f4c 68%,#4f8a2e 100%)"></div><div class="caption">Curabitur nisl ex, auctor in nisl in,<br>interdum porta urna<span class="price">1.250.000 €</span></div></article>
<article class="abs card" style="left:398px;top:865px"><div class="photo" role="img" aria-label="Glass-fronted villa reflected in a pool at sunset" style="background:linear-gradient(180deg,#5f6f92 0%,#d9b58c 25%,#f2efe8 45%,#c9ccd3 62%,#6a7a96 80%,#3a4a6a 100%)"></div><div class="caption">Curabitur nisl ex, auctor in nisl in,<br>interdum porta urna<span class="price">1.250.000 €</span></div></article>
<article class="abs card" style="left:553px;top:865px"><div class="photo" role="img" aria-label="Classic family home framed by trees and hedges" style="background:linear-gradient(180deg,#eef2f2 0%,#b9a488 30%,#8e7258 50%,#4f7a34 72%,#6fa044 100%)"></div><div class="caption">Curabitur nisl ex, auctor in nisl in,<br>interdum porta urna<span class="price">1.250.000 €</span></div></article>

<!-- footer -->
<footer>
  <div class="abs footer"></div>
  <h4 class="abs foot-head" style="left:86px">Links</h4>
  <ul class="abs foot-list" style="left:86px"><li>• Home</li><li>• Costa del sol</li><li>• Services</li><li>• Blog</li><li>• Contact Us</li></ul>
  <h4 class="abs foot-head" style="left:196px">Contact us</h4>
  <ul class="abs foot-list" style="left:196px"><li>• Phone : 612 480 9273</li><li>• Email : info@ventohallmark.example</li><li>• Support</li></ul>
  <h4 class="abs foot-head" style="left:362px">Newsletter Subscribe</h4>
  <div class="abs news-input">Email Address</div>
  <div class="abs news-btn">SUBMIT</div>
  <h4 class="abs foot-head" style="left:613px">Share us on</h4>
  <div class="abs social">
    <span style="background:#3b5998"></span><span style="background:#2aa3ef"></span><span style="background:#0e76a8"></span><span style="background:#5b7fa6"></span>
  </div>
  <div class="abs copy">Copyright © 2016 Vento Hallmark. &nbsp;All rights reserved.</div>
</footer>

</body>
</html>
```